Eyecatching website design for commercial lighting business

This contest is all about the graphic design aspect. We need a striking website design for a commercial lighting company. We want something really eye catching to introduce people to our range of induction and LED lights which save businesses money on maintenance and electricity costs.

To be successful in this contest you will need to provide a design and pictures for the pages listed below.

We are using the platform velbrin.com.au and you can see the attached template which everything will be loaded into so we just need HTML files which we can upload and we can do everything else from Velbrin.

The final design should be strong and clean and use the colours and textures in the attached business card file.

Detailed requirements:

Please see attached screenshot of the website template, all we need is a fantastic graphic design and improvement/ incorporation of our logo for the following pages
Page Headings:
1. Home
About Us, Contact Us, snapshot of and link to Blog

Each of the below pages will have several paragraphs of text followed by a list of suitable products which is generated from our product catalogue.

2. Car Park Lighting
3. Educational Lighting
4. Hospitality Lighting
5. Office & Shop Lighting
6. Warehouse Lighting

Some of the website we have seen which are similar in nature are:
http://www.quorvanlamps.com.au/
http://www.tibrox.com/
http://www.gandowlumen.net/commercial-led
but we really want a modern, eye catching and memorable design

Some of the designs built on Velbrin that we like are:

http://www.pemberhollow.com.au/
http://www.marwickgoods.com.au/
http://www.kelmorabay.com.au/

I've also uploaded a couple of photos that we love. We'd like something similar for each industry.

Target Market(s)

Company Owners, Maintenance & Facilities Managers, Electrical Contractors

Industry/Entity Type

Electrical

Coding

Coded - Design and coding required

Number of Pages Required

5+ page

Font styles to use
Sans Serif

Colors
33a6d7
ec1f27

Requirements
Must have
• -Must scale to mobile
• -HTML coded files need to be provided (HTML Bootstrap)
Nice to have
• -Prefer incorporation of our logo into header bar
• -Design of 2-3 advertising banners which can be displayed on the home page
• -Prominent call to action button towards top of page 'Get a quote' or similar
• -Grid based design HTML Bootstrap

```html
<!DOCTYPE html>
<html lang="en">
<head>
<meta charset="utf-8">
<title>Lumarc Solutions — Commercial Lighting</title>
<link rel="stylesheet" href="https://fonts.googleapis.com/css2?family=Open+Sans:wght@400;600;700&family=Oswald:wght@500;600&display=swap">
<style>
:root{
  --red:#ec1f27;
  --red-deep:#a5141a;
  --blue:#33a6d7;
  --ink:#1b1b1d;
  --charcoal:#2a2a2c;
  --white:#ffffff;
  --muted:#b9b9bb;
}
*{box-sizing:border-box;margin:0;padding:0}
html,body{width:820px;height:1200px;overflow:hidden}
body{font-family:"Open Sans",Arial,sans-serif;color:var(--white);background:var(--ink)}
.page{position:relative;width:820px;height:1200px}

/* header */
.site-header{position:absolute;top:0;left:0;right:0;height:56px;display:flex;align-items:center;justify-content:space-between;padding:0 40px;z-index:2;background:rgba(20,10,14,.35)}
.brand{display:flex;align-items:center;gap:10px}
.brand-mark{width:22px;height:22px;border-radius:50%;background:var(--red)}
.brand-name{font-family:"Open Sans",Arial,sans-serif;font-weight:700;font-size:13px;letter-spacing:2px;text-transform:uppercase;color:var(--white)}
.main-nav{display:flex;align-items:center;gap:4px;font-size:11px}
.main-nav a{color:var(--white);text-decoration:none;padding:8px 12px}
.main-nav a.active{background:var(--red)}
.search-icon{margin-left:8px}

/* hero */
.hero{position:absolute;top:0;left:0;width:820px;height:520px}
.hero-photo{position:absolute;inset:0;background:linear-gradient(180deg,#3a2530 0%,#6a2a36 35%,#7a2430 60%,#3c1a22 100%)}
.hero-content{position:absolute;left:72px;top:180px;width:600px}
.hero-title{font-family:"Oswald",Arial,sans-serif;font-weight:600;font-size:33px;letter-spacing:.5px;line-height:1.1}
.hero-text{margin-top:10px;font-size:15px;line-height:1.45;color:#f0e4e6}
.btn-read{display:inline-block;margin-top:18px;background:var(--red);color:var(--white);font-size:10px;font-weight:700;padding:8px 14px;text-decoration:none;letter-spacing:.5px}
.scroll-down{position:absolute;left:398px;top:408px}

/* about */
.about{position:absolute;top:520px;left:0;width:820px;height:205px;background:linear-gradient(180deg,#3a3a3d,#262628 70%,#1c1c1e);text-align:center;padding-top:34px}
.section-title{font-family:"Oswald",Arial,sans-serif;font-weight:500;font-size:17px;letter-spacing:1px;text-transform:uppercase}
.title-rule{width:90px;height:1px;background:var(--muted);margin:8px auto 0;opacity:.6}
.about-text{width:640px;margin:26px auto 0;font-size:9px;line-height:1.8;color:var(--muted)}

/* solutions */
.solutions{position:absolute;top:725px;left:0;width:820px;height:245px;background:var(--ink);text-align:center;padding-top:30px}
.solution-grid{display:flex;justify-content:center;gap:26px;margin-top:20px}
.solution-card{width:210px}
.solution-photo{height:110px}
.photo-car{background:linear-gradient(180deg,#1d4d8c,#4f8fd0 60%,#1e2a45)}
.photo-edu{background:radial-gradient(circle at 50% 45%,#f4f4f0,#9da1a6 45%,#5f6368)}
.photo-hosp{background:linear-gradient(180deg,#d9d4c8,#a8a092 60%,#6e675c)}
.solution-label{background:var(--red);font-size:8px;font-weight:700;padding:8px 0;letter-spacing:.3px}

/* video & blog */
.video-blog{position:absolute;top:970px;left:0;width:820px;height:190px;background:linear-gradient(180deg,#c81820,var(--red-deep));padding-top:18px}
.video-blog .section-title{text-align:center}
.video-blog .title-rule{background:#f0b0b3}
.vb-row{display:flex;gap:24px;padding:0 72px;margin-top:16px}
.video-card{width:235px;flex:none}
.video-photo{height:100px;background:linear-gradient(180deg,#1d1a24,#3c3030 60%,#6b4a24);display:flex;align-items:center;justify-content:center}
.video-label{background:var(--red);font-size:8px;font-weight:700;padding:6px 0;text-align:center}
.blog-post h3{font-size:9px;font-weight:700;text-transform:uppercase;line-height:1.4}
.blog-post p{font-size:8px;line-height:1.65;margin-top:6px;color:#f6d4d6}
.blog-meta{font-size:8px;margin-top:6px;color:#ffd9db}

/* footer */
.site-footer{position:absolute;top:1160px;left:0;width:820px;height:40px;background:#141416;display:flex;align-items:center;justify-content:space-between;padding:0 40px;font-size:8px;color:var(--muted)}
.social{display:flex;gap:8px}
.social span{width:26px;height:12px;background:#3b3b3f;border-radius:2px}
</style>
</head>
<body>
<div class="page">

  <section class="hero">
    <div class="hero-photo" role="img" aria-label="Container port at dusk under floodlights with a red tint"></div>
    <div class="hero-content">
      <h1 class="hero-title">ON THE OTHER HAND, WE DENOUNCE</h1>
      <p class="hero-text">Indignation and dislike men who are so beguiled and demoralized by the charms of pleasure of the moment, so blinded by desire</p>
      <a class="btn-read" href="#">READ MORE &gt;&gt;</a>
    </div>
    <svg class="scroll-down" width="24" height="24" viewBox="0 0 24 24" aria-hidden="true">
      <circle cx="12" cy="12" r="10.5" fill="none" stroke="#fff" stroke-width="1.5"/>
      <path d="M7.5 10l4.5 4.5 4.5-4.5" fill="none" stroke="#fff" stroke-width="2"/>
    </svg>
  </section>

  <header class="site-header">
    <div class="brand">
      <span class="brand-mark"></span>
      <span class="brand-name">Lumarc Solutions</span>
    </div>
    <nav class="main-nav">
      <a class="active" href="#">Home</a>
      <a href="#">About us</a>
      <a href="#">Products</a>
      <a href="#">Blog</a>
      <a href="#">Contact us</a>
      <a href="#">Login</a>
      <svg class="search-icon" width="12" height="12" viewBox="0 0 12 12" aria-hidden="true">
        <circle cx="5" cy="5" r="3.6" fill="none" stroke="#fff" stroke-width="1.4"/>
        <path d="M7.7 7.7l3.3 3.3" stroke="#fff" stroke-width="1.6"/>
      </svg>
    </nav>
  </header>

  <section class="about" role="region" aria-label="About us">
    <h2 class="section-title">About Us</h2>
    <div class="title-rule"></div>
    <p class="about-text">At vero eos et accusamus et iusto odio dignissimos ducimus qui blanditiis praesentium voluptatum deleniti atque corrupti quos dolores et quas molestias excepturi sint occaecati cupiditate non provident, similique sunt in culpa qui officia deserunt mollitia animi, id est laborum et dolorum fuga. Et harum quidem rerum facilis est et expedita distinctio.</p>
  </section>

  <section class="solutions">
    <h2 class="section-title">Lighting Solutions</h2>
    <div class="title-rule"></div>
    <div class="solution-grid">
      <div class="solution-card">
        <div class="solution-photo photo-car" role="img" aria-label="Lit car park at night"></div>
        <div class="solution-label">CAR PARK LIGHTING</div>
      </div>
      <div class="solution-card">
        <div class="solution-photo photo-edu" role="img" aria-label="Glowing light bulb"></div>
        <div class="solution-label">EDUCATIONAL LIGHTING</div>
      </div>
      <div class="solution-card">
        <div class="solution-photo photo-hosp" role="img" aria-label="Bright hotel lobby interior"></div>
        <div class="solution-label">HOSPITALITY LIGHTING</div>
      </div>
    </div>
  </section>

  <section class="video-blog">
    <h2 class="section-title">Video &amp; Blog</h2>
    <div class="title-rule"></div>
    <div class="vb-row">
      <div class="video-card">
        <div class="video-photo" role="img" aria-label="Video still of a lit warehouse at night">
          <svg width="26" height="26" viewBox="0 0 26 26" aria-hidden="true">
            <circle cx="13" cy="13" r="12" fill="rgba(0,0,0,.45)"/>
            <path d="M10 8l8 5-8 5z" fill="#fff"/>
          </svg>
        </div>
        <div class="video-label">Warehouse Lighting Tour</div>
      </div>
      <article class="blog-post">
        <h3>Sed ut perspiciatis unde omnis iste natus error sit voluptatem</h3>
        <p>Nam libero tempore, cum soluta nobis est eligendi optio cumque nihil impedit quo minus id quod maxime placeat facere possimus, omnis voluptas assumenda est, omnis dolor repellendus. Temporibus autem quibusdam et aut officiis debitis aut rerum necessitatibus saepe eveniet ut et voluptates repudiandae sint.</p>
        <p class="blog-meta">Posted 20 Jan 2015 by Lumarc Admin in Lighting</p>
      </article>
    </div>
  </section>

  <footer class="site-footer">
    <span>© Lumarc 2015 All rights reserved</span>
    <div class="social"><span></span><span></span><span></span><span></span><span></span></div>
  </footer>

</div>
</body>
</html>
```